Rig up a website for a Rigging Company

We already have a logo. Looking for a website design that works on pavlune.com.
Our rigging company uses semi trucks, forklifts, and similar equipment to move large machines.
Our logo is white, black and red.

Target Market(s)

Medical Industry (moving medical equipment), Utility Industry (power equipment), Food Industry (moving bottling/packing equipment), US Government (large equipment)

Industry/Entity Type

It Company

Coding

Coded - Design and coding required

Number of Pages Required

5+ page

Font styles to use
Sans Serif

Colors
ec1f27
ffffff
0355a3

Requirements
Must have
• Home page, About page, Services Page, and Contact Information page
Nice to have
• Pictures of semi and forklifts and ability to insert our own pictures of our equipment

```html
<!DOCTYPE html>
<html lang="en">
<head>
<meta charset="utf-8">
<title>Halvern Rigging</title>
<link href="https://fonts.googleapis.com/css2?family=Open+Sans:wght@400;600;700;800&display=swap" rel="stylesheet">
<style>
:root{
  --red:#ec1f27;
  --ink:#1b1b1b;
  --text:#666;
  --white:#fff;
  --foot:#f4f4f4;
  --line:#d6d6d6;
}
*{margin:0;padding:0;box-sizing:border-box}
html,body{width:743px;height:1200px;overflow:hidden;background:var(--white)}
body{position:relative;font-family:"Open Sans",Arial,sans-serif;color:var(--text)}
.abs{position:absolute}
.brand{display:flex;align-items:center;gap:6px;font-weight:800;color:var(--ink);font-size:18px;letter-spacing:-.3px;line-height:1;white-space:nowrap}
.brand i{display:block;width:10px;height:10px;background:var(--red)}
.call{right:82px;top:12px;font-size:7px;color:var(--ink)}
.call b{color:var(--red);font-weight:400}
.nav a{position:absolute;top:38px;font-size:7px;color:var(--ink);text-decoration:none;white-space:nowrap}
.nav a.on{color:var(--red)}
.hero{left:0;top:55px;width:743px;height:286px;background:linear-gradient(180deg,#9ea1a5 0%,#cfd0d2 45%,#b9b7b2 100%)}
.hero-card{left:82px;top:153px;width:230px;height:135px;background:rgba(80,80,80,.55);padding:14px 19px}
.hero-card h1{font-weight:400;font-size:19.5px;color:var(--white);line-height:1.2;white-space:nowrap;letter-spacing:-.2px}
.hero-card p{font-size:7px;color:var(--white);line-height:12px;margin-top:10px;width:205px}
.btn{display:inline-flex;align-items:center;justify-content:center;background:var(--red);color:var(--white);font-size:7px;border-radius:2px;box-shadow:0 1px 2px rgba(0,0,0,.25)}
.arrow{width:30px;height:30px;background:rgba(60,60,60,.6);display:flex;align-items:center;justify-content:center}
.h2{width:743px;left:0;text-align:center;font-weight:400;color:var(--red);font-size:19px}
.welcome-p{left:128px;top:410px;width:487px;text-align:center;font-size:6.6px;line-height:12px}
.band{left:0;top:529px;width:743px;height:261px;background:var(--red)}
.card{top:622px;width:186px;height:127px;overflow:hidden}
.card span{position:absolute;left:0;bottom:0;width:100%;height:33px;background:rgba(70,70,70,.55);color:var(--white);font-size:12px;text-align:center;line-height:33px}
.news-img{top:874px;width:107px;height:90px}
.news-h{top:870px;font-size:12px;color:var(--red);font-weight:400}
.news-p{top:896px;width:150px;font-size:6.8px;line-height:12px}
.footer{left:0;top:1010px;width:743px;height:190px;background:var(--foot)}
.fh{font-size:9px;color:var(--red);font-weight:400}
.fl{font-size:6.5px;color:var(--text);white-space:nowrap}
.ring{width:20px;height:20px;border:1.4px solid #333;border-radius:50%}
.input{left:360px;top:1090px;width:155px;height:26px;background:var(--white);border:1px solid var(--line);font-size:6.5px;padding:0 9px;line-height:24px}
</style>
</head>
<body>
<header>
  <div class="abs brand" style="left:83px;top:16px"><i></i>Halvern Rigging</div>
  <div class="abs call"><b>&#9742; CALL US :</b> 1800 555 0192</div>
  <nav class="nav">
    <a class="on" style="left:423px">HOME</a>
    <a style="left:467px">ABOUT US</a>
    <a style="left:526px">SERVICES</a>
    <a style="left:578px">NEWS</a>
    <a style="left:622px">CONTACT US</a>
  </nav>
</header>

<section class="abs hero" role="img" aria-label="Orange forklift inside a bright warehouse"></section>
<div class="abs hero-card">
  <h1>RIGGING COMPANY</h1>
  <p>Lorem ipsum dolor sit amet, consectetur adipiscing elit, sed do eiusmod tempor incididunt</p>
  <a class="btn" style="width:70px;height:22px;margin-top:14px">Request Quote</a>
</div>
<div class="abs arrow" style="left:36px;top:194px"><svg width="8" height="12"><path d="M6 1 1 6l5 5" fill="none" stroke="#fff" stroke-width="1"/></svg></div>
<div class="abs arrow" style="left:675px;top:194px"><svg width="8" height="12"><path d="M2 1l5 5-5 5" fill="none" stroke="#fff" stroke-width="1"/></svg></div>

<h2 class="abs h2" style="top:371px">WELCOME TO HALVERN RIGGING</h2>
<p class="abs welcome-p">Nemo enim ipsam voluptatem quia voluptas sit aspernatur aut odit aut fugit, sed quia consequuntur magni dolores eos qui ratione voluptatem sequi nesciunt. Neque porro quisquam est, qui dolorem ipsum quia dolor sit amet, consectetur, adipisci velit, sed quia non numquam eius modi tempora incidunt ut labore et dolore magnam aliquam quaerat voluptatem.</p>
<a class="abs btn" style="left:343px;top:466px;width:57px;height:21px">Read More</a>

<section class="abs band"></section>
<h2 class="abs h2" style="top:562px;color:var(--white);font-size:18px">OUR SERVICES</h2>
<div class="abs card" style="left:82px;background:linear-gradient(160deg,#c9ccd3,#4a5066 60%,#d8d8d8)" role="img" aria-label="Semi truck on the road"><span>SEMI TRUCKS</span></div>
<div class="abs card" style="left:279px;background:linear-gradient(160deg,#e8ecef,#9aa7ad 55%,#b5413c)" role="img" aria-label="Forklifts in a warehouse aisle"><span>FORKLIFTS</span></div>
<div class="abs card" style="left:478px;background:linear-gradient(160deg,#c5c7c4,#8f8a5a 55%,#3d3f3c)" role="img" aria-label="Large yellow machine in a warehouse"><span>LARGE MACHINES</span></div>

<h2 class="abs h2" style="top:814px">RECENT NEWS</h2>
<div class="abs news-img" style="left:82px;background:linear-gradient(150deg,#c9b799,#8d7a62 50%,#d9692f)" role="img" aria-label="Forklift between warehouse shelves"></div>
<h3 class="abs news-h" style="left:205px">LOREM IPSUM DOLOR</h3>
<p class="abs news-p" style="left:205px">Nemo enim ipsam voluptatem quia voluptas sit aspernatur aut odit aut fugit, sed quia consequuntur magni</p>
<a class="abs btn" style="left:206px;top:942px;width:57px;height:21px">Read More</a>
<div class="abs news-img" style="left:394px;background:linear-gradient(160deg,#b6b8ba,#8e8c88 50%,#c97a4f)" role="img" aria-label="Forklift among stacked goods in a warehouse"></div>
<h3 class="abs news-h" style="left:517px">LOREM IPSUM DOLOR</h3>
<p class="abs news-p" style="left:517px">Nemo enim ipsam voluptatem quia voluptas sit aspernatur aut odit aut fugit, sed quia consequuntur magni</p>
<a class="abs btn" style="left:518px;top:942px;width:57px;height:21px">Read More</a>

<footer class="abs footer"></footer>
<div class="abs brand" style="left:83px;top:1042px;font-size:15px"><i></i>Halvern Rigging</div>
<div class="abs ring" style="left:82px;top:1083px"></div>
<div class="abs ring" style="left:105px;top:1083px"></div>
<div class="abs ring" style="left:128px;top:1083px"></div>
<div class="abs ring" style="left:151px;top:1083px"></div>
<div class="abs ring" style="left:173px;top:1083px"></div>

<h4 class="abs fh" style="left:250px;top:1032px">QUICK LINKS</h4>
<span class="abs fl" style="left:251px;top:1053px">Home</span>
<span class="abs fl" style="left:251px;top:1068px">About us</span>
<span class="abs fl" style="left:251px;top:1083px">Services</span>
<span class="abs fl" style="left:251px;top:1097px">News</span>
<span class="abs fl" style="left:251px;top:1112px">Contact us</span>

<h4 class="abs fh" style="left:359px;top:1032px">NEWSLETTER</h4>
<span class="abs fl" style="left:361px;top:1053px">Enter your email address to receive the latest</span>
<span class="abs fl" style="left:361px;top:1068px">news and notes from our blog.</span>
<div class="abs input">Enter Your Mail Id</div>
<a class="abs btn" style="left:362px;top:1128px;width:51px;height:18px;font-size:6.5px">SUBSCRIBE</a>

<h4 class="abs fh" style="left:560px;top:1032px">CONTACT US</h4>
<svg class="abs" style="left:561px;top:1054px" width="8" height="60" fill="#555">
  <rect x="0" y="2" width="8" height="5" rx="1"/>
  <rect x="1" y="18" width="6" height="6"/>
  <rect x="0" y="35" width="8" height="5" fill="none" stroke="#555"/>
  <path d="M4 51a2.5 2.5 0 0 1 2.5 2.5C6.5 56 4 59 4 59S1.5 56 1.5 53.5A2.5 2.5 0 0 1 4 51z"/>
</svg>
<span class="abs fl" style="left:575px;top:1053px">(555) 240-7100</span>
<span class="abs fl" style="left:575px;top:1070px">(555) 240-7100</span>
<span class="abs fl" style="left:575px;top:1087px;text-decoration:underline">info@halvernmail.com</span>
<span class="abs fl" style="left:575px;top:1104px;white-space:normal;width:90px;line-height:8px">#4170 Quarry Lane, Suite 12, Eastfield</span>

<div class="abs" style="left:83px;top:1162px;width:579px;height:1px;background:var(--line)"></div>
<p class="abs fl" style="left:0;width:743px;text-align:center;top:1175px;color:#333">&copy;2017 Halvern Rigging. All Rights Reserved.</p>
</body>
</html>
```